Lucky Harbour Fun Casino Entertainment

Looking to update my business card and make it look more modern, stand out and eye catching.
We are are fun casino business in Australia (primarily Sydney). Blackjack and Roulette are our most popular games although we have pretty much every game available for hire that you would find in a real casino. The final design would need to be sleek and appeal to the more upmarket corporate sector.
We mainly cater for Corporate Events, Private Parties, Fundraising Events, Team Building, Poker Tournaments
I think I'd prefer the colour Black.

Target Market(s)

High-end Corporate

Industry/Entity Type

Events

Contact Information for Business Card

Rob Kendall
Director
1300 482 617
0433 728 591
info@luckyharbour.com.au
www.luckyharbour.com.au
Facebook & Instagram @luckyharbourevents (proper social icons preferred)

Colors
000000
0255a3

Requirements
Must have
• Front side:
• Logo
• Contact details
• 'Australia's #1 Fun Casino Specialists'
• Back:
• Logo
Nice to have
• Back:
• Corporate Events
• Private Parties
• Poker Tournaments
• Fundraising
• Props & Theming
• Photo Booth
• Horse Racing Events
• The Vegas Sign attached, maybe on the back of the card in the background...?

```html
<!DOCTYPE html>
<html lang="en">
<head>
<meta charset="utf-8">
<title>Lucky Harbour Fun Casino Entertainment – Business Card</title>
<link href="https://fonts.googleapis.com/css2?family=Lato:wght@400;700&display=swap" rel="stylesheet">
<style>
  :root {
    --backdrop: #2b2522;
    --card: #0f0f0f;
    --card-edge: #1c1c1c;
    --accent: #f5a623;
    --text: #c9c9c9;
    --muted: #9a9a9a;
    --divider: #2c2c2c;
  }
  * { box-sizing: border-box; margin: 0; padding: 0; }
  html, body { width: 1200px; height: 844px; overflow: hidden; }
  body {
    background: var(--backdrop);
    font-family: "Lato", sans-serif;
    position: relative;
  }
  .card {
    position: absolute;
    top: 262px;
    width: 540px;
    height: 320px;
    background: var(--card);
    border: 1px solid var(--card-edge);
    box-shadow: 0 10px 30px rgba(0,0,0,.45);
  }
  .card--front { left: 45px; }
  .card--back { left: 615px; }

  .brand {
    display: flex;
    align-items: center;
    gap: 10px;
    color: var(--accent);
    font-weight: 700;
    font-size: 24px;
    letter-spacing: .5px;
    white-space: nowrap;
  }
  .brand__dot {
    width: 34px; height: 34px;
    border-radius: 50%;
    background: var(--accent);
    flex: none;
  }

  .card--front .brand {
    position: absolute;
    left: 32px;
    top: 140px;
  }
  .card__divider {
    position: absolute;
    left: 262px;
    top: 40px;
    width: 1px;
    height: 240px;
    background: var(--divider);
  }
  .contact {
    position: absolute;
    left: 290px;
    top: 58px;
  }
  .contact__name {
    color: var(--accent);
    font-weight: 700;
    font-size: 21px;
    letter-spacing: .3px;
    line-height: 1.1;
  }
  .contact__role {
    color: var(--muted);
    font-size: 14px;
    margin-bottom: 8px;
  }
  .contact__list { list-style: none; }
  .contact__item {
    display: flex;
    align-items: center;
    gap: 7px;
    color: var(--text);
    font-size: 15px;
    line-height: 21px;
  }
  .contact__item svg { flex: none; }
  .contact__social { margin-top: 12px; }
  .contact__social .contact__item { line-height: 24px; }
  .social-dot {
    width: 17px; height: 17px;
    border-radius: 50%;
    background: #4a6fa8;
    flex: none;
  }

  .card--back .brand {
    position: absolute;
    left: 50%;
    top: 96px;
    transform: translateX(-50%);
    font-size: 28px;
  }
  .tagline {
    position: absolute;
    left: 0; right: 0;
    top: 226px;
    text-align: center;
    color: var(--accent);
    font-size: 15px;
    letter-spacing: .8px;
  }
</style>
</head>
<body>

  <section class="card card--front" aria-label="Business card front">
    <div class="brand"><span class="brand__dot"></span>Lucky Harbour</div>
    <div class="card__divider"></div>
    <div class="contact">
      <p class="contact__name">ROB KENDALL</p>
      <p class="contact__role">Director</p>
      <ul class="contact__list">
        <li class="contact__item">
          <svg width="12" height="12" viewBox="0 0 12 12" aria-hidden="true"><path d="M1 4c0-2 2-3 5-3s5 1 5 3l-2 1-1-1.5H4L3 5 1 4zM2.5 6h7l1 5h-9z" fill="var(--accent)"/></svg>
          1300 482 617
        </li>
        <li class="contact__item">
          <svg width="12" height="12" viewBox="0 0 12 12" aria-hidden="true"><rect x="1.5" y="1.5" width="9" height="9" rx="1.5" fill="none" stroke="var(--accent)" stroke-width="1.6"/></svg>
          0433 728 591
        </li>
        <li class="contact__item">
          <svg width="12" height="12" viewBox="0 0 12 12" aria-hidden="true"><rect x="1" y="2.5" width="10" height="7" fill="var(--accent)"/><path d="M1 2.5l5 4 5-4" fill="none" stroke="var(--card)" stroke-width="1"/></svg>
          info@luckyharbour.com.au
        </li>
        <li class="contact__item">
          <svg width="12" height="12" viewBox="0 0 12 12" aria-hidden="true"><circle cx="6" cy="6" r="5" fill="var(--accent)"/><path d="M1 6h10M6 1c-2 2-2 8 0 10M6 1c2 2 2 8 0 10" fill="none" stroke="var(--card)" stroke-width=".8"/></svg>
          www.luckyharbour.com.au
        </li>
      </ul>
      <ul class="contact__list contact__social">
        <li class="contact__item"><span class="social-dot"></span>@luckyharbourevents</li>
        <li class="contact__item"><span class="social-dot"></span>@luckyharbourevents</li>
      </ul>
    </div>
  </section>

  <section class="card card--back" aria-label="Business card back">
    <div class="brand"><span class="brand__dot"></span>Lucky Harbour</div>
    <p class="tagline">AUSTRALIA'S #1 FUN CASINO SPECIALISTS</p>
  </section>

</body>
</html>
```